Private Investment Firm Needs PowerPoint Presentation Template

Design PowerPoint template, take Pinebrook-submitted rough presentation draft, and drop it into new template. See attached Project Brief file for more detail.
Updates

Some decent designs have been submitted but they seem to lack the understanding of our target markets. I am hopeful that more time and feedback will result in better results.

Target Market(s)

Private company owners and intermediaries.

Font styles to use
Serif

Colors
3176b5

Requirements
Must have
• See attached Project Brief.
Nice to have
Should not have
• No B2C fluff--this is a B2B project.

```html
<!DOCTYPE html>
<html lang="en">
<head>
<meta charset="utf-8">
<title>Pinebrook Capital – Presentation Slides</title>
<link rel="stylesheet" href="https://fonts.googleapis.com/css2?family=Lato:wght@400;700;900&family=Libre+Baskerville&family=Tinos&display=swap">
<style>
:root{
  --navy:#1f4e6b;
  --teal:#178a7a;
  --blue:#3176b5;
  --panel-blue:#5b9bd5;
  --table-blue:#3a7dc4;
  --yellow:#f5b800;
  --red:#e0312f;
  --grey-text:#7f7f7f;
  --light:#f2f2f2;
  --row-grey:#d9d9d9;
  --ink:#1b1b1b;
}
*{margin:0;padding:0;box-sizing:border-box}
html,body{width:1200px;height:1010px;overflow:hidden;background:#fff;font-family:'Lato',sans-serif;color:var(--ink)}
.deck{position:relative;width:1200px;height:1010px}
.slide{position:absolute;width:600px;height:337px;overflow:hidden;background:#fff}
.s13{left:0;top:0}.s14{left:600px;top:0}.s15{left:0;top:337px}
.s16{left:600px;top:337px}.s17{left:0;top:674px}.s18{left:600px;top:674px}
.abs{position:absolute}
.wordmark{position:absolute;display:flex;align-items:center;gap:4px;font-family:'Libre Baskerville',serif;color:var(--navy);font-size:10px;letter-spacing:1px}
.wordmark i{display:block;width:12px;height:12px;border-radius:50%;background:var(--blue)}
.page-no{position:absolute;width:24px;height:24px;border-radius:50%;background:var(--teal);color:#fff;font-size:8px;display:flex;align-items:center;justify-content:center;border:2px solid #fff;box-shadow:0 0 0 1px #ccc}
.dots{display:flex;gap:5px;justify-content:center}
.dots span{width:7px;height:7px;border-radius:50%;background:#c8c8c8}
/* slide 13 */
.s13 h1{position:absolute;left:40px;top:10px;width:520px;text-align:center;font-size:23px;line-height:25px;font-weight:900;color:var(--navy)}
.s13 .dots{position:absolute;left:0;width:600px;top:63px}
.case{position:absolute;border:1px solid #b9c3cc;background:#fff;padding:4px 6px 3px 48px;font-size:5.6px;line-height:6.6px;text-align:center;color:#222}
.case b{display:block;font-size:6.3px;margin-bottom:1px}
.case-mark{position:absolute;width:68px;height:68px;border-radius:50%;background:var(--teal);border:2px solid #0f6d60;display:flex;align-items:center;justify-content:center;text-align:center;color:#fff;font-weight:700;font-size:8px;line-height:9px;padding:4px}
/* slide 14 */
.arrow-tag{position:absolute;color:#fff;font-weight:900;font-size:11px;line-height:13px}
.s14 .lead{position:absolute;left:20px;top:126px;width:220px;text-align:center;font-size:23px;line-height:27px;font-weight:900;color:var(--navy)}
.crit{position:absolute;left:325px;font-size:9px;color:var(--ink)}
/* slide 15 */
.value-panel{position:absolute;left:29px;top:28px;width:539px;height:272px;background:var(--panel-blue)}
.value-panel h2{position:absolute;left:60px;top:12px;width:460px;text-align:center;font-size:23px;line-height:28px;font-weight:900;color:#fff}
.value-panel h2 em{font-style:normal;color:var(--navy)}
.value-panel .dots{position:absolute;left:0;width:539px;top:72px}
.value-panel .dots span{background:#fff}
.value-list{position:absolute;left:33px;top:92px;width:500px;list-style:none;color:#fff;font-size:12.3px;line-height:18.2px}
.value-list li::before{content:"•";margin-right:9px}
.value-list li.cont::before{content:"";margin:0}
.note-tag{position:absolute;left:342px;top:250px;width:250px;padding:3px 6px;background:#fff;border:1px solid var(--blue);color:var(--blue);font-style:italic;font-weight:700;font-size:9.5px;line-height:11px;text-align:center;transform:rotate(-20deg)}
/* slide 16 */
.s16 .lead{position:absolute;left:34px;top:114px;width:220px;font-size:23px;line-height:27px;font-weight:900;color:var(--grey-text)}
.s16 .lead strong{color:var(--navy)}
.impact{position:absolute;left:274px;top:64px;width:326px;border-collapse:collapse;font-size:10.5px}
.impact th{background:var(--table-blue);color:#fff;font-weight:700;height:62px;text-align:center;line-height:13px}
.impact th:first-child{text-align:center}
.impact td{height:37px;vertical-align:top;padding:3px 4px;line-height:12px}
.impact td+td{text-align:center}
.impact tr:nth-child(odd) td{background:var(--row-grey)}
.impact tr:nth-child(even) td{background:var(--light)}
.impact-note{position:absolute;left:274px;top:239px;width:326px;text-align:center;font-family:'Tinos',serif;font-size:7.6px;line-height:9px}
/* slide 17 */
.summary-panel{position:absolute;left:19px;top:42px;width:565px;height:260px;background:var(--light)}
.s17 h2{position:absolute;left:31px;top:52px;font-size:35px;font-weight:900;color:#fff}
.summary-list{position:absolute;left:222px;top:62px;width:360px;font-size:11.6px;line-height:14.8px;color:var(--ink);list-style:none}
.summary-list li{position:relative;padding-left:13px}
.summary-list li::before{content:"•";position:absolute;left:0}
.summary-list ul{list-style:none;font-size:10.6px;line-height:13px}
.summary-list ul li{margin-left:10px}
.summary-list a{color:var(--blue);text-decoration:none}
.summary-list .out{margin-left:-16px}
/* slide 18 */
.photo{position:absolute;left:4px;top:1px;width:594px;height:336px;background:linear-gradient(135deg,#8a8f93 0%,#a68a6a 40%,#7c5f45 70%,#5b5f63 100%)}
.epilogue{position:absolute;left:49px;top:86px;width:214px;height:120px;border-radius:50%;background:#fff;display:flex;align-items:center;justify-content:center;font-size:26px;color:var(--navy);letter-spacing:1px}
</style>
</head>
<body>
<div class="deck">

<!-- Representative investments -->
<section class="slide s13">
  <h1>Pinebrook Representative Non-Control Capital Investments</h1>
  <div class="dots"><span></span><span></span><span></span></div>

  <div class="case" style="left:44px;top:83px;width:252px;height:70px"><b>Growth Capital</b>Operates dedicated commercial airline pilot training facilities across the U.S. and Mexico, with classrooms, procedures trainers and full-motion flight simulators. Pinebrook's capital funded near-term growth and the company added key management personnel.</div>
  <div class="case-mark" style="left:2px;top:84px">Skyline Flight</div>

  <div class="case" style="left:338px;top:83px;width:260px;height:70px"><b>Management Buy-Out (MBO)</b>Provider of audit compliance software and consulting services for hospitals and physician practices. Pinebrook helped the active CEO acquire the business from its inactive founder and invested in its core revenue integrity software platform.</div>
  <div class="case-mark" style="left:306px;top:84px">Hollis</div>

  <div class="case" style="left:44px;top:163px;width:252px;height:70px"><b>Acquisition Finance</b>Manufacturer of vibration isolation, seismic control and shock protection products. Pinebrook's capital allowed it to acquire two tuck-in companies, a testing lab and an online component distributor. Three years later the company set an all-time sales record.</div>
  <div class="case-mark" style="left:2px;top:164px">Vantor Group</div>

  <div class="case" style="left:338px;top:163px;width:260px;height:70px"><b>Balance Sheet Recapitalization</b>Provider of third-party vehicle maintenance services for private, public and for-hire fleets nationwide. Pinebrook provided subordinated debt and preferred stock to support growth beyond the lender's capacity, and the company grew significantly.</div>
  <div class="case-mark" style="left:306px;top:164px">Fleetwise</div>

  <div class="case" style="left:44px;top:245px;width:252px;height:72px"><b>Family Ownership &amp; Wealth Transfer</b>Provider of fire and security alarm design, installation and monitoring services. Pinebrook's capital gave the CEO room to think strategically; five years later the family bought out Pinebrook's ownership with senior debt and now owns 100% of the company.</div>
  <div class="case-mark" style="left:2px;top:246px">Summit Alarm</div>

  <div class="case" style="left:338px;top:245px;width:260px;height:72px"><b>Family Office Support</b>Provides comprehensive and custom packaging for the liquid home cleaning products sector, safely processing volatile liquids such as bleach and hydrogen peroxide. Pinebrook assisted a New York-based family office in acquiring the company as part of its growth strategy.</div>
  <div class="case-mark" style="left:306px;top:246px">Orion Corporation</div>

  <div class="wordmark" style="left:4px;top:318px"><i></i>PINEBROOK</div>
  <div class="page-no" style="left:574px;top:309px">13</div>
</section>

<!-- Investment criteria -->
<section class="slide s14">
  <svg class="abs" style="left:0;top:0" width="600" height="337" aria-hidden="true">
    <polygon points="232,10 300,337 228,337" fill="#eef1f4"/>
    <polygon points="0,30 53,30 53,16 110,52 53,88 53,74 0,74" fill="var(--teal)"/>
    <g>
      <rect x="290" y="87" width="32" height="18" rx="9" fill="#3a78c0"/>
      <rect x="282" y="119" width="40" height="18" rx="9" fill="var(--yellow)"/>
      <rect x="274" y="149" width="48" height="18" rx="9" fill="var(--red)"/>
      <rect x="266" y="181" width="56" height="18" rx="9" fill="#3a78c0"/>
      <rect x="258" y="215" width="64" height="18" rx="9" fill="var(--yellow)"/>
      <rect x="246" y="248" width="76" height="18" rx="9" fill="var(--red)"/>
      <rect x="236" y="281" width="86" height="18" rx="9" fill="#3a78c0"/>
    </g>
  </svg>
  <div class="arrow-tag" style="left:5px;top:40px">INVESTMENT<br>CRITERIA</div>
  <p class="lead">Pinebrook invests in established, lower middle market companies</p>
  <p class="crit" style="top:91px">Revenues of $10MM to $150MM</p>
  <p class="crit" style="top:122px">EBITDA of at least $2MM</p>
  <p class="crit" style="top:153px">Pinebrook investment size of $5MM to $25MM</p>
  <p class="crit" style="top:185px">Experienced, committed, and incented management</p>
  <p class="crit" style="top:219px">Limited leverage (aka debt) “ahead” of Pinebrook</p>
  <p class="crit" style="top:252px">Niche market leader with differentiated services or products</p>
  <p class="crit" style="top:285px;left:327px">Focused on value-added execution, not proof of concept</p>
  <div class="wordmark" style="left:8px;top:305px"><i></i>PINEBROOK</div>
  <div class="page-no" style="left:570px;top:309px">14</div>
</section>

<!-- Value creation -->
<section class="slide s15">
  <div class="value-panel">
    <h2><em>WE HELP</em> PORTFOLIO COMPANIES CREATE GREATER VALUE</h2>
    <div class="dots"><span></span><span></span><span></span></div>
    <ul class="value-list">
      <li>Facilitate strategy development</li>
      <li>Improve financial reporting and information systems</li>
      <li>Assist with key hires, such as CFOs and COOs, if needed</li>
      <li>Source, evaluate, finance, close, and integrate acquisitions</li>
      <li>Invest additional capital</li>
      <li>Annual Executive Summit focused on professional development and networking</li>
      <li>Most importantly, act as a sounding board to help solve problems,</li>
      <li class="cont" style="margin-left:-14px">identify new opportunities, and create value</li>
      <li>We personally invest in every transaction</li>
    </ul>
  </div>
  <svg class="abs" style="left:0;top:48px" width="112" height="68" aria-hidden="true">
    <polygon points="0,12 52,12 52,0 110,34 52,68 52,56 0,56" fill="var(--teal)"/>
  </svg>
  <div class="arrow-tag" style="left:3px;top:68px;font-size:10.5px">CONSULTANTS<br>&nbsp;WITH CAPITAL</div>
  <div class="note-tag">These options are made available to our portfolio companies, if needed, and not forced upon them</div>
  <div class="wordmark" style="left:4px;top:302px"><i></i>PINEBROOK</div>
  <div class="page-no" style="left:573px;top:309px">15</div>
</section>

<!-- Impact by the numbers -->
<section class="slide s16">
  <svg class="abs" style="left:0;top:0" width="250" height="100" aria-hidden="true">
    <polygon points="0,30 182,30 182,18 242,53 182,88 182,76 0,76" fill="var(--teal)"/>
  </svg>
  <div class="arrow-tag" style="left:20px;top:45px;width:170px;text-align:center;font-size:10.5px">PINEBROOK IMPACT - BY THE NUMBERS</div>
  <p class="lead">During Pinebrook’s average investment term, <strong>our impact has been noteworthy</strong></p>
  <table class="impact">
    <tr><th>Impact Category</th><th>Actual<br>Impact</th><th>Min/Max*<br>Removed</th></tr>
    <tr><td>Average Revenue Growth</td><td>113%</td><td>91%</td></tr>
    <tr><td>Average EBITDA Growth</td><td>75%</td><td>78%</td></tr>
    <tr><td>Average Employee Growth</td><td>213%</td><td>49%</td></tr>
  </table>
  <p class="impact-note">*Note: Actual Impact figures based on 55 exited investments from 1994 to 2017.<br>Min/Max removed from each of 3 fully invested funds.</p>
  <div class="wordmark" style="left:8px;top:306px"><i></i>PINEBROOK</div>
  <div class="page-no" style="left:569px;top:304px">16</div>
</section>

<!-- Summary -->
<section class="slide s17">
  <div class="summary-panel"></div>
  <svg class="abs" style="left:0;top:0" width="260" height="337" aria-hidden="true">
    <polygon points="19,21 238,21 148,313 19,313" fill="var(--blue)"/>
    <polygon points="238,21 248,42 232,42" fill="#1f5f96"/>
    <circle cx="100" cy="170" r="60" fill="var(--teal)"/>
    <rect x="76" y="138" width="44" height="58" rx="4" fill="#15252e"/>
    <rect x="81" y="146" width="34" height="45" fill="var(--teal)"/>
    <rect x="89" y="132" width="18" height="10" rx="3" fill="#15252e"/>
    <g stroke="#15252e" stroke-width="2.4" fill="none">
      <path d="M85 155l2 2 4-4M95 156h15M85 166l2 2 4-4M95 167h15M85 177l2 2 4-4M95 178h12"/>
    </g>
    <circle cx="121" cy="193" r="13" fill="#15252e"/>
    <path d="M114 193l5 5 9-9" stroke="#fff" stroke-width="3" fill="none"/>
  </svg>
  <h2>SUMMARY</h2>
  <ul class="summary-list">
    <li>There is an alternative to giving up control of your company through an infusion of Non-Control Capital</li>
    <li>All investors are not created equal</li>
    <li>Non-Control Capital investing is a specialty:
      <ul><li>Choose only an investor with decades of Non-Control heritage, experience, and focus (<a>see Questionnaire in the Epilogue section of this presentation</a>)</li></ul>
    </li>
    <li class="out">It means more than just capital:
      <ul><li>Team up with an accomplished investor who can bring demonstrated growth abilities, not simply write a check</li></ul>
    </li>
    <li class="out">Chemistry between company management and the investor is critical:
      <ul><li>If Pinebrook’s interests are not aligned with management, we don’t invest</li></ul>
    </li>
  </ul>
  <div class="wordmark" style="left:14px;top:311px;font-size:8px"><i style="width:9px;height:9px"></i>PINEBROOK</div>
  <div class="page-no" style="left:570px;top:309px">17</div>
</section>

<!-- Epilogue -->
<section class="slide s18">
  <div class="photo" role="img" aria-label="Overhead photo of a business meeting table with laptops, notebooks and a handshake"></div>
  <div class="epilogue">EPILOGUE</div>
</section>

</div>
</body>
</html>
```